KBT Business Cards

We require business cards for our business. We would like a matte black back to the card, with our logo centred in the middle. The front side of the card is open to design.

Target Market(s)

Clients looking for legal services (professional)

Industry/Entity Type

Legal

Contact Information for Business Card

Doran Kelbrath
Partner
Mobile: 0461 738 524
Email: doran@kbtlaw.co
Website: www.kbtlaw.co
Level 3, 118 Wendmore Street
Sydney NSW 2000

Font styles to use
Other font styles liked:
• Avenir

Colors
f04a50
ffffff
1b1b1b

Requirements
Must have
• Black back with logo included in the centre of the card.
• Our font is Avenir.

```html
<!DOCTYPE html>
<html lang="en">
<head>
<meta charset="utf-8">
<title>KBT Law — Business Cards</title>
<link rel="stylesheet" href="https://fonts.googleapis.com/css2?family=Nunito+Sans:wght@400;600;800&display=swap">
<style>
  :root {
    --ink: #1b1b1b;
    --black: #0e0e0e;
    --white: #ffffff;
    --crimson: #c8173f;
    --stage: #2a2a2a;
    --muted: #e6e6e6;
    --font: "Nunito Sans", "Avenir", Arial, sans-serif;
  }
  * { box-sizing: border-box; margin: 0; padding: 0; }
  html, body {
    width: 1200px; height: 960px; overflow: hidden;
    background: var(--stage);
    font-family: var(--font);
  }
  .canvas { position: relative; width: 1200px; height: 960px; }

  .card {
    position: absolute; left: 280px;
    width: 640px; height: 388px;
    border-radius: 6px; overflow: hidden;
  }

  /* Back of card */
  .card-back {
    top: 64px;
    background: radial-gradient(ellipse at 50% 40%, #242424 0%, #141414 55%, var(--black) 100%);
  }
  .back-brand {
    position: absolute; left: 0; right: 0; top: 148px;
    display: flex; justify-content: center; align-items: center; gap: 16px;
  }
  .brand-square { width: 34px; height: 34px; background: var(--crimson); }
  .back-brand .brand-name {
    color: var(--white); font-weight: 800; font-size: 44px;
    letter-spacing: 1px; line-height: 1;
  }
  .back-url {
    position: absolute; left: 0; right: 0; bottom: 52px;
    text-align: center; color: var(--white);
    font-size: 15px; letter-spacing: 5px;
  }
  .back-url .accent { color: var(--crimson); font-weight: 600; }

  /* Front of card */
  .card-front { top: 508px; background: var(--white); }
  .front-shapes { position: absolute; inset: 0; }
  .front-brand {
    position: absolute; left: 52px; top: 152px;
    display: flex; align-items: center; gap: 14px;
  }
  .front-brand .brand-square { width: 26px; height: 26px; }
  .front-brand .brand-name {
    color: var(--ink); font-weight: 800; font-size: 38px;
    letter-spacing: 1px; line-height: 1;
  }
  .contact {
    position: absolute; right: 40px; top: 92px;
    text-align: right; color: var(--white);
  }
  .contact-name { font-size: 22px; font-weight: 800; letter-spacing: 1px; text-transform: uppercase; }
  .contact-role { font-size: 14px; letter-spacing: 1px; margin-top: 2px; }
  .contact-address { font-size: 15px; line-height: 1.35; margin-top: 12px; color: var(--muted); }
  .contact-lines { list-style: none; margin-top: 16px; font-size: 15px; color: var(--muted); }
  .contact-lines li {
    display: flex; justify-content: flex-end; align-items: center;
    gap: 8px; line-height: 1.7;
  }
  .contact-lines svg { width: 15px; height: 15px; }
</style>
</head>
<body>
<main class="canvas">

  <section class="card card-back" aria-label="Card back">
    <div class="back-brand">
      <span class="brand-square"></span>
      <span class="brand-name">KBT LAW</span>
    </div>
    <p class="back-url">www.<span class="accent">kbtlaw</span>.co</p>
  </section>

  <section class="card card-front" aria-label="Card front">
    <svg class="front-shapes" viewBox="0 0 640 388" width="640" height="388" aria-hidden="true">
      <circle cx="606" cy="200" r="286" fill="var(--crimson)"/>
      <circle cx="612" cy="204" r="280" fill="var(--white)"/>
      <circle cx="620" cy="206" r="274" fill="var(--black)"/>
    </svg>

    <div class="front-brand">
      <span class="brand-square"></span>
      <span class="brand-name">KBT LAW</span>
    </div>

    <div class="contact">
      <p class="contact-name">Doran Kelbrath</p>
      <p class="contact-role">PARTNER</p>
      <p class="contact-address">Level 3, 118 Wendmore Street<br>Sydney NSW 2000</p>
      <ul class="contact-lines">
        <li>0461 738 524
          <svg viewBox="0 0 16 16" aria-hidden="true"><circle cx="8" cy="8" r="7.2" fill="none" stroke="#fff" stroke-width="1"/><rect x="5.5" y="3.5" width="5" height="9" rx="1" fill="none" stroke="#fff" stroke-width="1"/></svg>
        </li>
        <li>doran@kbtlaw.co
          <svg viewBox="0 0 16 16" aria-hidden="true"><rect x="2" y="4" width="12" height="8" fill="#fff"/><path d="M2 4 L8 9 L14 4" fill="none" stroke="#0e0e0e" stroke-width="1"/></svg>
        </li>
        <li>www.kbtlaw.co
          <svg viewBox="0 0 16 16" aria-hidden="true"><circle cx="8" cy="8" r="7" fill="none" stroke="#fff" stroke-width="1"/><ellipse cx="8" cy="8" rx="3" ry="7" fill="none" stroke="#fff" stroke-width="1"/><path d="M1 8 H15 M2.5 4.5 H13.5 M2.5 11.5 H13.5" stroke="#fff" stroke-width="1"/></svg>
        </li>
      </ul>
    </div>
  </section>

</main>
</body>
</html>
```